Digital Billboard Design: Winter Sales Event

I own a boutique furniture store in Calgary, AB (larkhollowhome.ca) and I am looking to advertise our winter sale event on a new curved digital billboard (specs attached including required file type).

I have this billboard rented for 52-weeks so I will be looking to change the design every 4-weeks (i.e. this is intended to be an ongoing project).

The objective of this first billboard is to raise awareness around our annual winter sales event. The store itself is only a few blocks from the billboard so those commuting into downtown are just a short drive from the store.

I am looking for a fresh, clean, contemporary look that will grab your attention as you drive into downtown Calgary without presenting to much info so as to be distracting (and overwhelming -- the billboard does not need to contain all info on my current marketing material). I should also note that the store caters to a higher-end, more sophisticated clientele so the graphics need to reflect the brand (i.e. we are not Brenton Furniture or Couch Depot!).

I have attached three files:

Billboard specs
Current marketing material advertising sale (and all relevant data)
An idea that is from an American furniture store that I think is interesting

Target Market(s)

Upper middle class, sophisticated client who appreciates the finer things in life.

Industry/Entity Type

Furniture Store

Font styles to use
Sans Serif

Requirements
Must have
• Company Logo
• Winter Sales Event - 20 to 60% off
• Address: 2417 14th Ave SW
Nice to have
• Image of furniture -- see our website www.larkhollowhome.ca -- any photo from this site can be used
Should not have
• Too much text or visual distration

```html
<!DOCTYPE html>
<html lang="en">
<head>
<meta charset="utf-8">
<title>Lark Hollow Home — Winter Sales Event</title>
<link rel="stylesheet" href="https://fonts.googleapis.com/css2?family=Questrial&family=Rajdhani:wght@500;600&display=swap">
<style>
  :root {
    --page: #ffffff;
    --lime: #8cc63f;
    --white: #ffffff;
    --ink: #333336;
    --logo-grey: #5c5c5f;
    --dash: #a9a9a9;
    --photo-top: #9a8f52;
    --photo-mid: #a6cf3c;
    --photo-low: #2a2826;
  }
  html, body {
    margin: 0;
    width: 1200px;
    height: 1001px;
    overflow: hidden;
    background: var(--page);
  }
  .canvas {
    position: relative;
    width: 1200px;
    height: 1001px;
  }
  .billboard {
    position: absolute;
    left: 152px;
    top: 284px;
    width: 900px;
    height: 431px;
    border: 1px dashed var(--dash);
  }
  .feature-photo {
    position: absolute;
    left: 1px;
    top: 2px;
    width: 434px;
    height: 283px;
    background: linear-gradient(180deg, var(--photo-top) 0%, var(--photo-mid) 22%, var(--photo-mid) 50%, #4a4a3e 62%, var(--photo-low) 100%);
  }
  .feature-photo svg { position: absolute; inset: 0; }
  .sale-panel {
    position: absolute;
    left: 440px;
    top: 2px;
    width: 457px;
    height: 283px;
    overflow: hidden;
    background: var(--lime);
    color: var(--white);
    font-family: "Rajdhani", sans-serif;
  }
  .sale-title {
    position: absolute;
    left: 15px;
    top: 180px;
    margin: 0;
    font-weight: 600;
    font-size: 44px;
    line-height: 1;
    letter-spacing: 2px;
    white-space: nowrap;
  }
  .sale-offer {
    position: absolute;
    left: 15px;
    top: 230px;
    margin: 0;
    font-weight: 500;
    font-size: 32px;
    line-height: 1;
    letter-spacing: 8.9px;
    white-space: nowrap;
  }
  .store-name {
    position: absolute;
    left: 0;
    right: 0;
    top: 314px;
    margin: 0;
    text-align: center;
    font-family: "Questrial", sans-serif;
    font-size: 48px;
    line-height: 1;
    letter-spacing: 0.5px;
    color: var(--logo-grey);
    white-space: nowrap;
  }
  .store-address {
    position: absolute;
    left: 0;
    right: 0;
    top: 370px;
    margin: 0;
    text-align: center;
    font-family: "Rajdhani", sans-serif;
    font-weight: 500;
    font-size: 32px;
    line-height: 1;
    letter-spacing: 8.6px;
    color: var(--ink);
    white-space: nowrap;
  }
</style>
</head>
<body>
  <main class="canvas">
    <section class="billboard">
      <div class="feature-photo" role="img" aria-label="Photo of a lime-green cushioned wicker outdoor sectional sofa with pale blue and floral pillows beside a glass coffee table">
        <svg width="434" height="283" viewBox="0 0 434 283" aria-hidden="true">
          <g stroke="#ffffff" stroke-width="4">
            <line x1="180" y1="0" x2="180" y2="283"/>
            <line x1="327" y1="0" x2="327" y2="283"/>
            <line x1="0" y1="142" x2="434" y2="142"/>
          </g>
        </svg>
      </div>
      <div class="sale-panel">
        <h1 class="sale-title">WINTER SALES EVENT</h1>
        <p class="sale-offer">20 TO 60% OFF</p>
      </div>
      <p class="store-name">LARK HOLLOW HOME</p>
      <p class="store-address">2417 14TH AVE SW, CALGARY, AB.</p>
    </section>
  </main>
</body>
</html>
```